Business card for medical clinic

I need an upmarket, modern medical/health business card for my clinic

Contact Information for Business Card

name, address, email, qr code

```html
<!DOCTYPE html>
<html lang="en">
<head>
<meta charset="utf-8">
<title>Lumera Care Group – Business Card</title>
<link href="https://fonts.googleapis.com/css2?family=Poppins:wght@300;400;600&display=swap" rel="stylesheet">
<style>
  :root {
    --stage: #232323;
    --card-white: #ecebea;
    --brand-blue: #1f8fcb;
    --brand-blue-deep: #1a6ea3;
    --ink: #1b1b1d;
    --navy: #1d3f66;
    --card-black: #141518;
    --pattern-grey: #2a2c31;
  }
  * { margin: 0; padding: 0; box-sizing: border-box; }
  html, body {
    width: 1200px; height: 780px; overflow: hidden;
    background: var(--stage);
    font-family: "Poppins", sans-serif;
  }
  .stage {
    position: relative; width: 1200px; height: 780px;
    display: flex; align-items: center; justify-content: center; gap: 60px;
  }
  .card {
    position: relative; width: 520px; height: 297px;
    border-radius: 18px; overflow: hidden;
  }

  /* Front */
  .card-front { background: var(--card-white); color: var(--ink); }
  .front-band { position: absolute; inset: 0; width: 100%; height: 100%; }
  .brand-name {
    position: absolute; font-family: "Poppins", sans-serif;
    font-weight: 600; color: var(--brand-blue-deep);
    letter-spacing: 2px; text-transform: uppercase; white-space: nowrap;
  }
  .card-front .brand-name { left: 280px; top: 66px; font-size: 17px; }
  .brand-dot {
    position: absolute; border-radius: 50%;
    background: var(--brand-blue-deep);
  }
  .card-front .brand-dot { left: 258px; top: 72px; width: 14px; height: 14px; }
  .person { position: absolute; left: 34px; top: 60px; }
  .person-name { font-size: 25px; color: var(--brand-blue); line-height: 1.1; }
  .person-name .first { font-weight: 600; }
  .person-name .last { font-weight: 300; }
  .person-title { font-size: 12px; font-weight: 400; margin-top: 6px; margin-left: 40px; }
  .divider {
    position: absolute; left: 232px; top: 128px;
    width: 1px; height: 72px; background: var(--brand-blue);
  }
  .contact-list { position: absolute; left: 252px; top: 132px; list-style: none; }
  .contact-item {
    display: flex; align-items: center; gap: 10px;
    font-size: 15px; line-height: 22px; color: var(--ink);
  }
  .contact-item svg { width: 14px; height: 14px; flex: none; }
  .address {
    position: absolute; left: 26px; bottom: 16px;
    font-size: 14px; font-weight: 300; color: #ffffff; letter-spacing: 0.3px;
  }

  /* Back */
  .card-back { background: var(--card-black); }
  .back-pattern {
    position: absolute; inset: 0;
    background: radial-gradient(ellipse at 70% 60%, var(--pattern-grey), var(--card-black) 75%);
  }
  .card-back .brand-name { left: 50%; top: 50%; transform: translate(-50%, -50%); font-size: 24px; color: var(--brand-blue); }
</style>
</head>
<body>
<main class="stage">

  <section class="card card-front" aria-label="Business card front">
    <svg class="front-band" viewBox="0 0 520 297" preserveAspectRatio="none" aria-hidden="true">
      <defs>
        <linearGradient id="bandFill" x1="0" y1="0" x2="1" y2="1">
          <stop offset="0" stop-color="#2aa0d8"/>
          <stop offset="1" stop-color="#1a6ea3"/>
        </linearGradient>
      </defs>
      <path d="M0,168 C110,215 300,262 480,297 L0,297 Z" fill="url(#bandFill)"/>
      <path d="M0,160 C110,205 300,252 470,288" fill="none" stroke="#ffffff" stroke-width="5"/>
      <path d="M4,150 C110,196 300,244 460,282" fill="none" stroke="#1d3f66" stroke-width="1.6"/>
    </svg>

    <span class="brand-dot" aria-hidden="true"></span>
    <span class="brand-name">Lumera Care Group</span>

    <div class="person">
      <p class="person-name"><span class="first">Marta</span> <span class="last">Kolarova</span></p>
      <p class="person-title">Founder &amp; CEO</p>
    </div>

    <span class="divider" aria-hidden="true"></span>

    <ul class="contact-list">
      <li class="contact-item">
        <svg viewBox="0 0 24 24" aria-hidden="true"><path fill="#1f8fcb" d="M6.6 10.8a15 15 0 0 0 6.6 6.6l2.2-2.2a1 1 0 0 1 1-.25 11.4 11.4 0 0 0 3.6.57 1 1 0 0 1 1 1V20a1 1 0 0 1-1 1A17 17 0 0 1 3 4a1 1 0 0 1 1-1h3.5a1 1 0 0 1 1 1c0 1.25.2 2.45.57 3.6a1 1 0 0 1-.25 1z"/></svg>
        (555) 214-6093
      </li>
      <li class="contact-item">
        <svg viewBox="0 0 24 24" aria-hidden="true"><rect x="2" y="5" width="20" height="14" rx="2" fill="#1f8fcb"/><path d="M3 6l9 7 9-7" fill="none" stroke="#fff" stroke-width="1.6"/></svg>
        hello@lumeracare.com
      </li>
      <li class="contact-item">
        <svg viewBox="0 0 24 24" aria-hidden="true"><circle cx="12" cy="12" r="10" fill="#1f8fcb"/><path d="M2 12h20M12 2c3 3 3 17 0 20M12 2c-3 3-3 17 0 20" fill="none" stroke="#fff" stroke-width="1.3"/></svg>
        www.lumeracare.com
      </li>
    </ul>

    <p class="address">418 Willow Bend Rd. Suite 120 Denton, TX 76201</p>
  </section>

  <section class="card card-back" aria-label="Business card back">
    <div class="back-pattern" role="img" aria-label="Embossed repeating pattern across the black card"></div>
    <span class="brand-name">Lumera Care Group</span>
  </section>

</main>
</body>
</html>
```